Rollers & Glides.com

Vertical Business Card with focus on branding with our icon. Information on card will be logo, persons name, position, phone number, email address and website. Use the the name Marcus Pellow, position President, phone number 480.915.2267, email Marcus@rollersandglides-demo.com, website www.rollersandglides-demo.com.

```html
<!DOCTYPE html>
<html lang="en">
<head>
<meta charset="UTF-8">
<title>Rollers &amp; Glides.com — Business Card</title>
<link rel="stylesheet" href="https://fonts.googleapis.com/css2?family=Roboto:wght@400;500;700&display=swap">
<style>
  :root {
    --bg: #d1d5d7;
    --paper: #f1f1ef;
    --brand-blue: #1e4ba0;
    --ink-navy: #13297e;
    --ink-grey: #3b3b3b;
    --white: #ffffff;
  }
  * { margin: 0; padding: 0; box-sizing: border-box; }
  html, body {
    width: 1200px; height: 1050px; overflow: hidden;
    background: var(--bg);
    font-family: "Roboto", Arial, sans-serif;
  }
  .canvas {
    width: 1200px; height: 1050px;
    display: flex; flex-direction: column;
    align-items: center; justify-content: center; gap: 70px;
  }
  .card {
    width: 700px; height: 400px;
    position: relative;
    box-shadow: 0 14px 30px rgba(0,0,0,0.18);
  }
  .card--front { background: var(--paper); }
  .card--back { background: var(--brand-blue); display: flex; align-items: center; justify-content: center; }

  .contact-block { position: absolute; left: 70px; top: 76px; }
  .person-name { color: var(--ink-navy); font-weight: 700; font-size: 26px; letter-spacing: 0.2px; }
  .person-role { color: var(--ink-grey); font-weight: 400; font-size: 22px; margin-top: 2px; }
  .rule { width: 28px; height: 2px; background: var(--ink-navy); margin: 16px 0 14px; }
  .contact-list { list-style: none; }
  .contact-item {
    display: flex; align-items: center; gap: 9px;
    color: var(--ink-grey); font-size: 19px; line-height: 1.55;
  }
  .contact-icon { width: 17px; height: 17px; flex: none; }

  .brand-mark {
    position: absolute; right: 56px; bottom: 64px;
    display: flex; align-items: center; gap: 12px;
    color: var(--ink-navy); font-weight: 500; font-size: 26px;
    white-space: nowrap;
  }
  .brand-dot { width: 16px; height: 16px; border-radius: 50%; background: var(--ink-navy); flex: none; }

  .brand-wordmark {
    display: flex; align-items: center; gap: 16px;
    color: var(--white); font-weight: 500; font-size: 40px; letter-spacing: 0.5px;
    white-space: nowrap;
  }
  .brand-wordmark .brand-dot { width: 24px; height: 24px; background: var(--white); }
</style>
</head>
<body>
<main class="canvas">
  <section class="card card--front">
    <div class="contact-block">
      <h1 class="person-name">Marcus Pellow</h1>
      <p class="person-role">President</p>
      <div class="rule"></div>
      <ul class="contact-list">
        <li class="contact-item">
          <svg class="contact-icon" viewBox="0 0 24 24" aria-hidden="true"><path fill="#13297e" d="M3 8c0-2 4-4 9-4s9 2 9 4v2h-5V8.5c-2.5-.8-5.5-.8-8 0V10H3z M6 12h12l2 8H4z"/></svg>
          <span>480.915.2267</span>
        </li>
        <li class="contact-item">
          <svg class="contact-icon" viewBox="0 0 24 24" aria-hidden="true"><path fill="#13297e" d="M2 6h20v13H2z"/><path fill="none" stroke="#f1f1ef" stroke-width="1.8" d="M2.5 6.5 12 13l9.5-6.5"/></svg>
          <span>Marcus@rollersandglides-demo.com</span>
        </li>
        <li class="contact-item">
          <svg class="contact-icon" viewBox="0 0 24 24" aria-hidden="true"><circle cx="12" cy="12" r="10" fill="#13297e"/><path fill="none" stroke="#f1f1ef" stroke-width="1.4" d="M2 12h20M12 2c-4 4-4 16 0 20M12 2c4 4 4 16 0 20"/></svg>
          <span>www.rollersandglides-demo.com</span>
        </li>
      </ul>
    </div>
    <div class="brand-mark">
      <span class="brand-dot"></span>
      <span>Rollers &amp; Glides.com</span>
    </div>
  </section>

  <section class="card card--back">
    <div class="brand-wordmark">
      <span class="brand-dot"></span>
      <span>Rollers &amp; Glides.com</span>
    </div>
  </section>
</main>
</body>
</html>
```